New Business Card Design

We would like to refresh our business cards and make them look better. We are an IT company specialising in Cloud Services, IT Managed Services, software and hardware. I have attached a PSD of our current design. Also attached our logo.
Updates

I have uploaded all new logos in EPS format.

Can you please edit all designs to include a job title for Marcus Hollis, eg. General Manager

Industry/Entity Type

Software

Colors
ffffff

Requirements
Must have
• Please use white background.
Should not have
• Black background

```html
<!DOCTYPE html>
<html lang="en">
<head>
<meta charset="utf-8">
<title>Clearpoint Systems – Business Card</title>
<link rel="stylesheet" href="https://fonts.googleapis.com/css2?family=Open+Sans:wght@300;400;600;700&display=swap">
<style>
  :root {
    --brand-red: #ec1c24;
    --accent-orange: #f5a11c;
    --accent-rust: #d9451f;
    --ink: #1e1e1e;
    --slate: #7b7f86;
    --soft-grey: #9aa0a6;
    --paper: #ffffff;
    --frame: #dfe8cf;
    --canvas: #ffffff;
  }
  * { margin: 0; padding: 0; box-sizing: border-box; }
  html, body {
    width: 1200px; height: 370px; overflow: hidden;
    background: var(--canvas);
    font-family: "Open Sans", Arial, sans-serif;
  }
  .sheet { position: relative; width: 1200px; height: 370px; }

  /* Front of card */
  .card-front {
    position: absolute; left: 26px; top: 34px; width: 560px; height: 310px;
    background: var(--brand-red); overflow: hidden;
  }
  .front-wordmark { position: absolute; left: 60px; top: 58px; display: flex; align-items: center; gap: 22px; }
  .wordmark-dot { width: 72px; height: 72px; border-radius: 50%; background: var(--paper); }
  .wordmark-text { color: var(--paper); font-weight: 300; line-height: 1; }
  .wordmark-name { font-size: 40px; letter-spacing: 8px; }
  .wordmark-sub { font-size: 18px; letter-spacing: 5px; margin-top: 8px; padding-left: 40px; }
  .front-ornament {
    position: absolute; left: 0; top: 150px; width: 200px; height: 160px;
    background: radial-gradient(ellipse at 20% 80%, rgba(255,150,120,0.55), rgba(236,28,36,0) 70%);
  }
  .service-list { position: absolute; list-style: none; color: var(--paper); font-size: 13px; }
  .service-list li { position: absolute; white-space: nowrap; }
  .service-list li::before {
    content: ""; display: inline-block; width: 6px; height: 6px; border-radius: 50%;
    background: var(--paper); margin-right: 10px; vertical-align: middle; position: relative; top: -2px;
  }

  /* Back of card */
  .card-back {
    position: absolute; left: 618px; top: 32px; width: 574px; height: 314px;
    background: var(--paper); border: 1px solid var(--frame);
  }
  .holder { position: absolute; right: 92px; top: 43px; text-align: right; }
  .holder-name { font-size: 24px; line-height: 1; font-weight: 400; }
  .holder-first { color: var(--accent-orange); }
  .holder-last { color: var(--accent-rust); font-weight: 700; }
  .holder-rule { position: absolute; left: 362px; top: 71px; width: 178px; height: 1px; background: var(--accent-orange); }
  .holder-title { position: absolute; right: 92px; top: 75px; font-size: 11px; color: var(--slate); font-weight: 600; }

  .contact { position: absolute; right: 92px; text-align: right; white-space: nowrap; }
  .contact-phone { font-size: 19px; color: var(--slate); display: flex; align-items: center; gap: 10px; }
  .phone-badge {
    width: 20px; height: 20px; border-radius: 50%; background: var(--brand-red);
    color: var(--paper); font-size: 12px; font-weight: 700; display: inline-flex;
    align-items: center; justify-content: center;
  }
  .contact-email { font-size: 18px; color: var(--ink); }
  .contact-web { font-size: 18px; color: var(--slate); }

  .back-wordmark { position: absolute; left: 12px; top: 238px; display: flex; align-items: center; gap: 10px; }
  .back-wordmark .wordmark-dot { width: 38px; height: 38px; background: var(--brand-red); }
  .back-wordmark .wordmark-text { color: var(--ink); }
  .back-wordmark .wordmark-name { font-size: 21px; letter-spacing: 3px; }
  .back-wordmark .wordmark-sub { font-size: 10px; letter-spacing: 3px; margin-top: 3px; padding-left: 20px; }

  .footer-rules { position: absolute; left: 212px; top: 282px; width: 320px; height: 2px; display: flex; gap: 3px; }
  .rule-red { flex: 0 0 232px; background: var(--brand-red); }
  .rule-ink { flex: 0 0 64px; background: var(--ink); }
  .rule-grey { flex: 1; background: var(--soft-grey); }
</style>
</head>
<body>
<main class="sheet">
  <section class="card-front" aria-label="Card front">
    <div class="front-wordmark">
      <span class="wordmark-dot"></span>
      <div class="wordmark-text">
        <div class="wordmark-name">clearpoint</div>
        <div class="wordmark-sub">SYSTEMS</div>
      </div>
    </div>
    <div class="front-ornament" role="img" aria-label="Soft coral floral flourish in the lower left corner"></div>
    <ul class="service-list">
      <li style="left:416px; top:186px;">Cloud Services</li>
      <li style="left:396px; top:212px;">Hardware</li>
      <li style="left:370px; top:238px;">Software</li>
      <li style="left:326px; top:260px;">IT Managed Services</li>
    </ul>
  </section>

  <section class="card-back" aria-label="Card back">
    <div class="holder">
      <div class="holder-name"><span class="holder-first">Marcus</span> <span class="holder-last">Hollis</span></div>
    </div>
    <div class="holder-rule"></div>
    <div class="holder-title">General Manager</div>

    <div class="contact contact-phone" style="top:120px;"><span class="phone-badge">M</span>07 3555 0148</div>
    <div class="contact contact-phone" style="top:146px;"><span class="phone-badge">P</span>0491 570 226</div>
    <div class="contact contact-email" style="top:180px;">mhollis@clearpointit.com.au</div>
    <div class="contact contact-web" style="top:222px;">www.clearpointit.com.au</div>

    <div class="back-wordmark">
      <span class="wordmark-dot"></span>
      <div class="wordmark-text">
        <div class="wordmark-name">clearpoint</div>
        <div class="wordmark-sub">SYSTEMS</div>
      </div>
    </div>

    <div class="footer-rules">
      <span class="rule-red"></span><span class="rule-ink"></span><span class="rule-grey"></span>
    </div>
  </section>
</main>
</body>
</html>
```